Verodex business card

Business card for sustainable investment company called "Verodex". Verodex is an exchange platform selling carbon credits between buyers and sellers. Carbon Credits are an environmental commodity for reducing global carbon emissions.

the card should obviously have our logo and the theme should be sustainability/environment mixed with a trading platform.

Contact Information for Business Card

Logo, Name, Title, Phone, Email

Colors
0054AA
0677BA
7BADD7
CADEEF
E8F1F8
0094D4
00A9DD
6FCCEA
C7EBF8
E9F6FB
00AB8E
00BBA5
67D7C9
C6EFE9
E9F9F6
59FF00
82FF00
B8FF75
E3FFCB
F4FFEA

```html
<!DOCTYPE html>
<html lang="en">
<head>
<meta charset="utf-8">
<title>Verodex business card</title>
<link rel="stylesheet" href="https://fonts.googleapis.com/css2?family=Open+Sans:wght@400;600;700;800&display=swap">
<style>
  :root {
    --stage: #232323;
    --card: #ffffff;
    --edge: #5fc8da;
    --navy: #13294f;
    --ink: #111111;
    --cyan: #67c8d8;
    --blue: #4a7fc6;
    --rule: #333333;
  }
  * { box-sizing: border-box; margin: 0; padding: 0; }
  html, body {
    width: 1200px; height: 780px; overflow: hidden;
    background: var(--stage);
    font-family: "Open Sans", Arial, sans-serif;
  }
  .canvas { position: relative; width: 1200px; height: 780px; }
  .card {
    position: absolute;
    width: 560px; height: 320px;
    background: var(--card);
    border-left: 6px solid var(--edge);
    box-shadow: 0 14px 30px rgba(0,0,0,.6);
  }
  .card--front { left: 90px; top: 70px; }
  .card--back { left: 550px; top: 390px; }

  .brand {
    position: absolute; left: 0; right: 0; top: 0; bottom: 0;
    display: flex; align-items: center; justify-content: center; gap: 18px;
  }
  .brand__mark {
    width: 46px; height: 46px; background: var(--blue);
  }
  .brand__name {
    font-weight: 800; font-size: 46px; letter-spacing: 2px;
    color: var(--navy); text-transform: uppercase;
  }

  .back__brand {
    position: absolute; left: 0; top: 0; width: 250px; height: 100%;
    display: flex; flex-direction: column; align-items: center; justify-content: center; gap: 14px;
  }
  .back__mark {
    width: 130px; height: 130px; border-radius: 50%;
    background: linear-gradient(135deg, var(--cyan), var(--blue));
  }
  .back__name { font-weight: 800; font-size: 26px; color: var(--blue); letter-spacing: 1px; }
  .divider {
    position: absolute; left: 262px; top: 60px; width: 1px; height: 200px;
    background: var(--rule);
  }
  .contact { position: absolute; left: 290px; top: 58px; }
  .contact__name {
    font-weight: 800; font-size: 25px; line-height: 1.1;
    background: linear-gradient(90deg, var(--cyan), var(--blue));
    -webkit-background-clip: text; background-clip: text; color: transparent;
  }
  .contact__title { font-weight: 700; font-size: 14px; color: var(--ink); margin-top: 2px; }
  .contact__address { font-size: 13px; color: var(--ink); line-height: 1.35; margin-top: 18px; }
  .contact__list { list-style: none; margin-top: 14px; }
  .contact__item {
    display: flex; align-items: center; gap: 9px;
    font-size: 13px; color: var(--ink); line-height: 1.55;
  }
  .contact__icon { width: 13px; height: 13px; flex: none; }
</style>
</head>
<body>
<main class="canvas">
  <section class="card card--front" aria-label="Card front">
    <div class="brand">
      <span class="brand__mark" aria-hidden="true"></span>
      <span class="brand__name">Verodex</span>
    </div>
  </section>

  <section class="card card--back" aria-label="Card back">
    <div class="back__brand">
      <span class="back__mark" aria-hidden="true"></span>
      <span class="back__name">Verodex</span>
    </div>
    <span class="divider" aria-hidden="true"></span>
    <div class="contact">
      <h1 class="contact__name">Lena Marovic</h1>
      <p class="contact__title">Managing Director</p>
      <p class="contact__address">418 Linden Ave. Suite 300<br>Arbor City, TX 75014</p>
      <ul class="contact__list">
        <li class="contact__item">
          <svg class="contact__icon" viewBox="0 0 16 16" aria-hidden="true"><path fill="#4a7fc6" d="M3.6 1.5l2.3 2.6-1.3 1.8c.9 2 2.5 3.6 4.5 4.5l1.8-1.3 2.6 2.3-1.4 2.3C7 13.4 2.6 9 1.3 2.9z"/></svg>
          (555) 214-3086
        </li>
        <li class="contact__item">
          <svg class="contact__icon" viewBox="0 0 16 16" aria-hidden="true"><rect x="1" y="3" width="14" height="10" rx="1" fill="#4a7fc6"/><path d="M1.5 3.8L8 9l6.5-5.2" fill="none" stroke="#fff" stroke-width="1.3"/></svg>
          info@verodex-mail.com
        </li>
        <li class="contact__item">
          <svg class="contact__icon" viewBox="0 0 16 16" aria-hidden="true"><circle cx="8" cy="8" r="7" fill="#4a7fc6"/><path d="M1 8h14M8 1c-2.5 2-2.5 12 0 14M8 1c2.5 2 2.5 12 0 14" fill="none" stroke="#fff" stroke-width="1"/></svg>
          www.verodex-site.com
        </li>
      </ul>
    </div>
  </section>
</main>
</body>
</html>
```